Kestrel Baseball & Softball Camp 2017

Design a flyer that will promote our 2017 summer camp for boys and girls softball.

Weeks of
July 10th - 14th
July 17th - 21st.

Players ages 5 - 11.
Full day = 9:30am - 2:30pm half day = 9:30am - 11:30am.
$295 / full day : $195/ half day

Hosted by "Kestrel Baseball" affiliated with the Harbor Comets Travel Baseball & Softball Club and the Maple Ridge Youth League,

Camp Location MRYL, Route 9C Birch Hollow.

PHone 555-240-7813, email info@kestrelball.example

The color should be "Red white and blue color scheme" with dates and location standing out. Kestrel Logo should be prominent MRYL and Comets smaller and secondary.

Feel free to use stock photo's if available. visit www.harborcomets.example for more pictures and there are links for the 2017 summer camp there with possibly some more information.

Target Market(s)

to catch the eye of parents of players ages 5 - 11 already at little league or shopping in local stores

Colors
ec1f27
0355a3
ffffff

Requirements
Must have
• red white and blue design,
• Kestrel logo and summer camp prominent so it catches the eye and explains what it is right away.
• the comets and maple ridge logo's a the bottom showing the affiliation.
Nice to have
• stock photo's or something showing players having a great time or a beautiful ballpark
Should not have
• to much clutter or hard to figure out what it's for

```html
<!DOCTYPE html>
<html lang="en">
<head>
<meta charset="utf-8">
<title>Kestrel Softball Summer Camp 2017</title>
<link href="https://fonts.googleapis.com/css2?family=Bebas+Neue&family=Kaushan+Script&family=Oswald:wght@600;700&display=swap" rel="stylesheet">
<style>
  :root{
    --red:#e31d25;
    --navy:#163a6e;
    --blue:#0355a3;
    --white:#ffffff;
    --dirt:#e7dbd0;
    --page:#d9d9d9;
    --ink:#1c1c1c;
  }
  *{margin:0;padding:0;box-sizing:border-box}
  html,body{width:1200px;height:1048px;overflow:hidden;background:var(--page)}
  .flyer{position:absolute;left:250px;top:24px;width:700px;height:1000px;background:var(--white);overflow:hidden;box-shadow:0 6px 18px rgba(0,0,0,.25)}
  .flyer-art{position:absolute;inset:0}
  .photo{position:absolute;left:0;top:0;width:700px;height:430px;background:linear-gradient(180deg,#2f86d6 0%,#5aa7e6 55%,#7fae78 80%,#3f7d3a 100%)}
  .logo-badge{position:absolute;left:400px;top:210px;width:212px;height:212px;border-radius:50%;background:var(--white);border:8px solid var(--red);display:flex;flex-direction:column;align-items:center;justify-content:center;text-align:center}
  .logo-badge .brand{font-family:"Oswald",sans-serif;font-weight:700;color:var(--red);font-size:40px;line-height:1;letter-spacing:1px;text-transform:uppercase}
  .logo-badge .brand small{display:block;font-size:17px;letter-spacing:.5px;margin-top:6px}
  .logo-badge .dot{width:14px;height:14px;border-radius:50%;background:var(--navy);margin-bottom:10px}
  .title{position:absolute;left:0;top:0;width:100%}
  .kicker{position:absolute;left:92px;top:448px;font-family:"Oswald",sans-serif;font-weight:600;font-size:26px;letter-spacing:11px;color:var(--navy)}
  .script-summer{position:absolute;left:52px;top:452px;font-family:"Kaushan Script",cursive;font-size:92px;color:var(--red);line-height:1}
  .camp{position:absolute;left:375px;top:440px;font-family:"Bebas Neue",sans-serif;font-size:118px;color:var(--navy);line-height:1;letter-spacing:1px}
  .year{position:absolute;left:636px;top:446px;font-family:"Bebas Neue",sans-serif;font-size:44px;color:var(--red);transform:rotate(90deg);transform-origin:left top;line-height:1;letter-spacing:2px;white-space:nowrap}
  .audience{position:absolute;left:362px;top:546px;font-family:"Kaushan Script",cursive;font-size:24px;color:var(--navy);transform:rotate(-4deg);white-space:nowrap}
  .rule{position:absolute;left:34px;top:550px;width:318px;height:2px;background:var(--red)}
  .weeks{position:absolute;left:105px;top:560px;font-family:"Bebas Neue",sans-serif;color:var(--navy)}
  .weeks .label{font-family:"Kaushan Script",cursive;font-size:19px;margin-left:2px}
  .weeks li{list-style:none;font-size:33px;line-height:37px;position:relative;padding-left:14px}
  .weeks li::before{content:"";position:absolute;left:0;top:13px;border-left:8px solid var(--red);border-top:5px solid transparent;border-bottom:5px solid transparent}
  .ages{position:absolute;left:420px;top:700px;display:flex;align-items:flex-start;font-family:"Bebas Neue",sans-serif;color:var(--navy);font-size:29px;line-height:34px}
  .ages .icon{margin-right:8px;margin-top:4px}
  .ages .words span{display:block}
  .age-badge{position:absolute;left:540px;top:680px;width:100px;height:100px;border-radius:50%;background:var(--navy);color:var(--white);font-family:"Bebas Neue",sans-serif;font-size:38px;display:flex;align-items:center;justify-content:center}
  .hours{position:absolute;left:84px;top:800px;display:flex;align-items:center;font-family:"Bebas Neue",sans-serif;color:var(--navy);font-size:24px;line-height:28px}
  .hours .icon{margin-right:12px}
  .cost{position:absolute;left:412px;top:795px;display:flex;align-items:center;font-family:"Bebas Neue",sans-serif;color:var(--navy);font-size:23px;line-height:28px}
  .cost .label{font-family:"Kaushan Script",cursive;font-size:17px;margin-right:10px;color:var(--ink)}
  .cost .icon{margin-right:14px}
  .divider{position:absolute;left:34px;top:862px;width:632px;border-top:2px dashed #333}
  .hosts{position:absolute;left:56px;top:884px;width:252px;height:70px;border:1.5px solid #222;padding:6px 6px;font-family:"Oswald",sans-serif;font-weight:600;font-size:7px;line-height:13px;color:var(--ink);text-align:center;text-transform:uppercase}
  .hosts span{display:block;white-space:nowrap}
  .partners{position:absolute;left:114px;top:926px;display:flex;gap:26px;align-items:center;background:var(--white);padding:0 8px}
  .partner-comets{width:84px;height:32px;background:var(--red);border-radius:4px}
  .partner-maple{width:36px;height:36px;border-radius:50%;background:#f2d23c;border:3px solid #3a8a3a}
  .info{position:absolute;top:890px;font-family:"Bebas Neue",sans-serif;color:var(--ink);font-size:16px;line-height:20px;white-space:nowrap}
  .info .label{display:flex;align-items:center;gap:8px;font-family:"Kaushan Script",cursive;font-size:16px;margin-bottom:4px;margin-left:-22px}
  .location{left:356px}
  .contact{left:498px}
</style>
</head>
<body>
<main class="flyer">
  <div class="photo" role="img" aria-label="Smiling young softball player holding a glove with a ball and a bat in front of a ballpark under blue sky"></div>

  <svg class="flyer-art" viewBox="0 0 700 1000" width="700" height="1000" aria-hidden="true">
    <path d="M0,392 C160,372 320,330 460,300 C560,278 640,240 700,215 L700,320 C600,340 480,360 380,378 C240,402 120,425 0,438 Z" fill="var(--navy)"/>
    <path d="M0,418 C200,398 420,355 700,298 L700,620 L0,780 Z" fill="var(--dirt)"/>
    <path d="M0,412 C200,392 430,350 700,290 L700,322 C470,375 230,420 0,446 Z" fill="var(--red)"/>
    <path d="M0,672 C200,700 450,640 700,560 L700,600 C460,680 230,735 0,755 Z" fill="var(--red)"/>
    <path d="M0,755 C230,735 460,680 700,600 L700,628 C470,705 240,760 0,782 Z" fill="#dcdcdc"/>
    <path d="M0,782 C240,760 470,705 700,628 L700,1000 L0,1000 Z" fill="var(--white)"/>
  </svg>

  <div class="logo-badge" aria-label="Kestrel Baseball">
    <span class="dot"></span>
    <span class="brand">Kestrel<small>Baseball</small></span>
  </div>

  <h1 class="title">
    <span class="kicker">SOFTBALL</span>
    <span class="script-summer">summer</span>
    <span class="camp">CAMP</span>
    <span class="year">2017</span>
  </h1>
  <div class="rule"></div>
  <p class="audience">for boys and girls</p>

  <div class="weeks">
    <span class="label">Weeks of</span>
    <ul>
      <li>July 10th - 14th</li>
      <li>July 17th - 21st.</li>
    </ul>
  </div>

  <div class="ages">
    <svg class="icon" width="26" height="28" viewBox="0 0 26 28" aria-hidden="true">
      <circle cx="6" cy="4" r="3.5" fill="var(--red)"/><rect x="2" y="9" width="8" height="10" rx="2" fill="var(--red)"/><rect x="3" y="18" width="2.5" height="9" fill="var(--red)"/><rect x="6.5" y="18" width="2.5" height="9" fill="var(--red)"/>
      <circle cx="19" cy="4" r="3.5" fill="var(--red)"/><path d="M15,9 H23 L25,20 H13 Z" fill="var(--red)"/><rect x="16" y="19" width="2.5" height="8" fill="var(--red)"/><rect x="19.5" y="19" width="2.5" height="8" fill="var(--red)"/>
    </svg>
    <div class="words"><span>Players</span><span>Ages</span></div>
  </div>
  <div class="age-badge">5 - 11</div>

  <div class="hours">
    <svg class="icon" width="26" height="30" viewBox="0 0 26 30" aria-hidden="true">
      <rect x="10" y="0" width="6" height="4" fill="var(--red)"/>
      <circle cx="13" cy="17" r="10.5" fill="none" stroke="var(--red)" stroke-width="3"/>
      <path d="M13,17 L13,10 M13,17 L18,20" stroke="var(--red)" stroke-width="2.5" fill="none" stroke-linecap="round"/>
    </svg>
    <div><div>Full day 9:30am - 2:30pm</div><div>Half day 9:30am - 11:30am</div></div>
  </div>

  <div class="cost">
    <span class="label">Cost:</span>
    <svg class="icon" width="30" height="30" viewBox="0 0 30 30" aria-hidden="true">
      <circle cx="15" cy="15" r="14" fill="var(--red)"/>
      <text x="15" y="21" text-anchor="middle" font-family="Oswald, sans-serif" font-weight="700" font-size="17" fill="#fff">$</text>
    </svg>
    <div><div>$295 / Full day</div><div>$195/ Half day</div></div>
  </div>

  <div class="divider"></div>

  <div class="hosts">
    <span>Hosted by "Kestrel Baseball" affiliated with the Harbor Comets Travel</span>
    <span>Baseball &amp; Softball Club and the Maple Ridge Youth League</span>
  </div>
  <div class="partners">
    <div class="partner-comets" role="img" aria-label="Harbor Comets badge"></div>
    <div class="partner-maple" role="img" aria-label="Maple Ridge Youth League badge"></div>
  </div>

  <div class="info location">
    <div class="label">
      <svg width="12" height="16" viewBox="0 0 12 16" aria-hidden="true"><path d="M6,0 C9.5,0 12,2.6 12,6 C12,10 6,16 6,16 C6,16 0,10 0,6 C0,2.6 2.5,0 6,0 Z" fill="#111"/><circle cx="6" cy="6" r="2.3" fill="#fff"/></svg>
      Camp Location:
    </div>
    <div>MRYL, Route 9C</div>
    <div>Birch Hollow.</div>
  </div>

  <div class="info contact">
    <div class="label">
      <svg width="12" height="18" viewBox="0 0 12 18" aria-hidden="true"><rect x="4" y="0" width="2" height="5" fill="#111"/><rect x="1" y="4" width="10" height="14" rx="2" fill="#111"/><rect x="3" y="7" width="6" height="4" fill="#fff"/></svg>
      Contact:
    </div>
    <div>Phone 555-240-7813</div>
    <div>Email info@kestrelball.example</div>
  </div>
</main>
</body>
</html>
```